Business Card Re-Design/Update

We'd like to update out business cards. I've included our current "Style guide" which has the colour scheme of the organisation in it. I've also included the branding files with logos etc in them.

I've also included a copy of one of our existing cards so that you can see how ugly/dated they look. I'd like a fresh modern corporate look.

Target Market(s)

These are for our clients, potential clients, industry contacts - like all business cards

Contact Information for Business Card

Name
Position
Company Address - Level 1, 47 Fernby Street, Carlow Qld 4072
Direct Phone
mobile
Email
Website -www.korvalit.com.au
Logo

Colors

Designer to choose colors to be used in the design.

Requirements
Must have
• Main Logo
• Cards will need to be editable to be able to personalize them for each new employee.
Nice to have
• The MapOut, ShipWell, KeepSteady would be okay to have if they can be sensibly and professionally added to the look without detracting from the main imagery.
• Maybe they could go on the back of the card? will leave this to your creative discretion as to whether/where they fit.
Should not have
• Should not have decorative or script fonts

```html
<!DOCTYPE html>
<html lang="en">
<head>
<meta charset="utf-8">
<title>korvalit business card</title>
<link rel="stylesheet" href="https://fonts.googleapis.com/css2?family=Work+Sans:wght@400;500;600&display=swap">
<style>
  :root {
    --page: #2b2c2e;
    --card-white: #ffffff;
    --card-fade: #ececec;
    --strip-light: #d9d9d9;
    --band-dark: #3a3b3d;
    --card-dark: #2f3032;
    --ink: #333436;
    --ink-soft: #555659;
    --brand-red: #d4141c;
    --logo-light: #c9c9c9;
  }
  * { box-sizing: border-box; margin: 0; padding: 0; }
  html, body { width: 1200px; height: 900px; overflow: hidden; }
  body {
    background: var(--page);
    font-family: "Work Sans", Arial, sans-serif;
    display: flex; flex-direction: column; align-items: center; justify-content: center;
    gap: 36px;
  }
  .card {
    position: relative;
    width: 700px; height: 400px;
    overflow: hidden;
    box-shadow: 0 14px 30px rgba(0,0,0,.45);
  }
  /* front */
  .card-front { background: radial-gradient(ellipse at 60% 60%, var(--card-white) 45%, var(--card-fade) 100%); }
  .top-strip { position: absolute; left: 0; top: 0; width: 100%; height: 26px; background: var(--strip-light); }
  .top-band { position: absolute; left: 0; top: 26px; width: 330px; height: 58px; background: var(--band-dark); }
  .brand {
    position: absolute; left: 318px; top: 74px;
    display: flex; align-items: center; gap: 14px;
  }
  .brand-square { width: 42px; height: 42px; background: var(--brand-red); }
  .brand-name { font-size: 66px; font-weight: 500; color: var(--ink); letter-spacing: -1px; line-height: 1; }
  .contacts { position: absolute; left: 38px; top: 176px; list-style: none; }
  .contacts li {
    display: flex; align-items: center; gap: 10px;
    font-size: 15px; color: var(--ink); line-height: 26px;
  }
  .contacts svg { width: 13px; height: 13px; fill: none; stroke: var(--brand-red); stroke-width: 2; }
  .contacts .web-accent { color: var(--brand-red); }
  .person { position: absolute; left: 400px; top: 230px; }
  .person-name { font-size: 30px; font-weight: 600; color: var(--brand-red); letter-spacing: 1px; }
  .person-role { font-size: 15px; color: var(--ink-soft); margin-top: 2px; letter-spacing: .5px; }
  .address { margin-top: 26px; font-size: 15px; color: var(--ink); line-height: 22px; letter-spacing: .5px; }
  /* back */
  .card-back { background: var(--card-dark); display: flex; align-items: center; justify-content: center; }
  .card-back .brand { position: static; }
  .card-back .brand-name { color: var(--logo-light); font-size: 76px; }
  .card-back .brand-square { width: 48px; height: 48px; }
</style>
</head>
<body>
  <section class="card card-front">
    <div class="top-strip"></div>
    <div class="top-band"></div>
    <div class="brand">
      <span class="brand-square"></span>
      <span class="brand-name">korvalit</span>
    </div>
    <ul class="contacts">
      <li><svg viewBox="0 0 14 14"><rect x="3.5" y="1" width="7" height="12" rx="1"/></svg>+61 (0)400 555 017</li>
      <li><svg viewBox="0 0 14 14"><path d="M2 5c0-2 10-2 10 0v2H9V5H5v2H2z"/><rect x="3" y="8" width="8" height="4"/></svg>+61 (0)7 3010 5521</li>
      <li><svg viewBox="0 0 14 14"><path d="M3 1l3 3-2 2c1 2 2 3 4 4l2-2 3 3-2 2C6 13 1 8 1 3z"/></svg>+61 (0)7 3010 5500</li>
      <li><svg viewBox="0 0 14 14"><rect x="2" y="5" width="10" height="7"/><rect x="4" y="1" width="6" height="4"/></svg>+61 (0)7 3010 5509</li>
      <li><svg viewBox="0 0 14 14"><rect x="1" y="3" width="12" height="8"/><path d="M1 3l6 5 6-5"/></svg>mellison@korvalit.com.au</li>
      <li><svg viewBox="0 0 14 14"><circle cx="7" cy="7" r="6"/><path d="M1 7h12M7 1c-3 3-3 9 0 12M7 1c3 3 3 9 0 12"/></svg>www.<span class="web-accent">korvalit</span>.com.au</li>
    </ul>
    <div class="person">
      <p class="person-name">MARA ELLISON</p>
      <p class="person-role">Business Development Manager</p>
      <p class="address">Level 1, 47 Fernby Street,<br>Carlow Qld 4072</p>
    </div>
  </section>

  <section class="card card-back">
    <div class="brand">
      <span class="brand-square"></span>
      <span class="brand-name">korvalit</span>
    </div>
  </section>
</body>
</html>
```